Redesign of business card for Cedar Ridge Mechanical

We are looking for a new design for our business cards for Cedar Ridge Mechanical. We are a plumbing & HVAC construction company, operating on the West Coast of Canada and USA. Logo attached.
Industry/Entity Type
Construction - Plumbing & HVAC
Contact Information for Business Card
Name, address, phone numbers, email, website address
Look and feel
Each slider illustrates characteristics of the customer's brand and the style your logo design should communicate.

```html
<!DOCTYPE html>
<html lang="en">
<head>
<meta charset="utf-8">
<title>Cedar Ridge Mechanical – Business Card</title>
<link rel="stylesheet" href="https://fonts.googleapis.com/css2?family=Roboto+Condensed:wght@500;700&family=Roboto:wght@400&display=swap">
<style>
  :root {
    --canvas: #dcdcdc;
    --card-front: #f6f6f6;
    --card-back: #333333;
    --ink: #111111;
    --ink-soft: #555555;
    --band-grey: #737373;
    --band-black: #0a0a0a;
    --white: #ffffff;
  }
  * { margin: 0; padding: 0; box-sizing: border-box; }
  html, body {
    width: 1200px; height: 1040px; overflow: hidden;
    background: var(--canvas);
  }
  .canvas { position: relative; width: 1200px; height: 1040px; }

  .card {
    position: absolute;
    border-radius: 18px;
    overflow: hidden;
  }
  .card--front {
    left: 286px; top: 130px; width: 640px; height: 366px;
    background: var(--card-front);
    color: var(--ink);
    font-family: "Roboto", Arial, sans-serif;
  }
  .card--back {
    left: 284px; top: 568px; width: 646px; height: 368px;
    background: var(--card-back);
  }

  .brand-name {
    font-family: "Roboto Condensed", "Arial Narrow", sans-serif;
    font-weight: 700;
    text-transform: uppercase;
    letter-spacing: 0.5px;
    line-height: 1;
  }
  .card--front .brand-name {
    position: absolute; right: 45px; top: 58px;
    font-size: 24px; text-align: right; color: var(--ink);
  }
  .card--back .brand-name {
    position: absolute; left: 0; right: 0; top: 158px;
    text-align: center; font-size: 42px; color: var(--white);
  }

  .holder-name {
    position: absolute; left: 42px; top: 208px;
    font-family: "Roboto Condensed", "Arial Narrow", sans-serif;
    font-weight: 700; font-size: 25px; line-height: 1;
  }
  .holder-title {
    position: absolute; left: 43px; top: 236px;
    font-size: 16px; color: var(--ink-soft); line-height: 1;
  }
  .divider {
    position: absolute; left: 42px; top: 260px; width: 553px; height: 1px;
    background: var(--ink);
  }
  .contact {
    position: absolute; left: 42px; top: 274px;
    list-style: none; font-size: 16px; line-height: 20px;
  }
  .contact li { display: flex; align-items: center; gap: 8px; }
  .contact svg { width: 13px; height: 13px; fill: var(--ink); flex: none; }
  .address {
    position: absolute; right: 45px; top: 276px;
    font-style: normal; text-align: right; font-size: 16px; line-height: 20px;
  }
  .footer-band { position: absolute; left: 0; top: 0; width: 640px; height: 366px; }
  .website {
    position: absolute; right: 45px; top: 337px;
    color: var(--white); font-size: 16px; line-height: 1;
  }
</style>
</head>
<body>
<main class="canvas">
  <section class="card card--front" aria-label="Business card front">
    <p class="brand-name">Cedar Ridge Mechanical</p>

    <h1 class="holder-name">Daniel Hartley</h1>
    <p class="holder-title">President</p>
    <div class="divider"></div>

    <ul class="contact">
      <li>
        <svg viewBox="0 0 24 24" aria-hidden="true"><path d="M6.6 10.8a15.1 15.1 0 0 0 6.6 6.6l2.2-2.2c.3-.3.7-.4 1-.2 1.1.4 2.3.6 3.6.6.6 0 1 .4 1 1V20c0 .6-.4 1-1 1A17 17 0 0 1 3 4c0-.6.4-1 1-1h3.5c.6 0 1 .4 1 1 0 1.3.2 2.5.6 3.6.1.3 0 .7-.2 1z"/></svg>
        (604) 5521-0187
      </li>
      <li>
        <svg viewBox="0 0 24 24" aria-hidden="true"><path d="M2 5h20v14H2zM4 7v.5l8 5 8-5V7zm0 2.8V17h16V9.8l-8 5z"/></svg>
        name@cedarridgemechanical.com
      </li>
    </ul>

    <address class="address">
      2417 Harbourview Road<br>
      Port Moody, BC V3H 1A2
    </address>

    <svg class="footer-band" viewBox="0 0 640 366" aria-hidden="true">
      <polygon points="0,335 362,335 346,350 0,350" fill="var(--band-grey)"/>
      <polygon points="372,326 640,326 640,366 0,366 0,353 342,353" fill="var(--band-black)"/>
    </svg>
    <p class="website">cedarridgemechanical.com</p>
  </section>

  <section class="card card--back" aria-label="Business card back">
    <p class="brand-name">Cedar Ridge Mechanical</p>
  </section>
</main>
</body>
</html>
```